Belvascotravel.com web design project + logo design

Hi,

We are a Russian online tour operator - sunkettle.com

We are looking to tranmsfer our domain to belvascotravel.com. The website and logo need to be belvascoesque - we are not looking to change our functionality, but we need to make the website much more attracitve to clients, much more wild looking but at the same time remaining a professional travel company.

The main concept of the website should be innovative travel (as belvasco was an innovator). Alternatively, you could go down the artist route and go down the draw / design your own tour road.

On our website the customer is able to combine travel services (hotels, flights, Visa services, and soon chauffeur, car rental etc...) put it into their basket (the basket definitely has to look better than it is at the moment) and pay for it in one go by card.

We are also stressin our customer support with web chat, call centre etc... (call centre number at the top of the page)

We aim to provide an easy user experience, but we need to make it have some more style, so I will be waiting for what you guys can come up with.
Let me know if you have any questions - skype is: mrdolbarin

Industry/Entity Type

It Company

Requirements
Must have
• It is quite a simple task - to take the existing website sunkettle.com and belvascosize it to create belvascotravel.com, the functionality of the website will remain the same and there are not many pages in the website. Homepage, Checkout step1, Checkout step 2 (you can view both of these if you select a service) and the generic pages for T&C''s, Privacy policy etc...

IMPORTANT UPDATE

We are also looking at how the search results will look in the designs, (please do a search on our website for hotel / flight)

```html
<!DOCTYPE html>
<html lang="en">
<head>
<meta charset="utf-8">
<title>Belvasco Travel</title>
<link href="https://fonts.googleapis.com/css2?family=Ubuntu:wght@400;500&family=Open+Sans:wght@300;400&display=swap" rel="stylesheet">
<style>
:root{
  --blue:#2f5fb3;
  --blue-dark:#1f4f9e;
  --panel:#4a74c2;
  --green:#2aa240;
  --green-dark:#1d8a33;
  --text:#8a8a8a;
  --text-dark:#333;
  --bg:#fafafa;
  --band:#f0f0f0;
  --footer:#24282d;
  --footer-line:#3a3f45;
  --tab:#e6e6e6;
}
*{box-sizing:border-box;margin:0;padding:0}
html,body{width:998px;height:1200px;overflow:hidden}
body{background:var(--bg);font-family:"Open Sans",sans-serif;color:var(--text);position:relative}
.abs{position:absolute}
a{color:inherit;text-decoration:none}

/* header */
.brand{left:100px;top:40px;display:flex;align-items:center;gap:8px;font-family:"Ubuntu",sans-serif;font-weight:500;font-size:19px;color:var(--blue)}
.brand-dot{width:34px;height:34px;border-radius:50%;background:var(--green)}
.social{top:18px;left:656px;display:flex;gap:9px}
.social span{width:20px;height:20px;border-radius:50%;background:#4a4a4a;display:flex;align-items:center;justify-content:center}
.callout{top:20px;left:752px;width:148px;text-align:center;font-family:"Ubuntu",sans-serif;font-size:12px;line-height:14px;color:#6a86b4}
.nav{top:62px;left:482px;display:flex;align-items:center;font-family:"Ubuntu",sans-serif;font-size:12px;color:var(--blue)}
.nav a{margin-right:45px}
.nav a:last-child{margin-right:0}
.nav .active{background:var(--green);color:#fff;border-radius:3px;padding:4px 16px;margin-right:27px}

/* hero */
.hero{left:100px;top:103px;width:547px;height:261px;background:linear-gradient(180deg,#7fb6e6 0%,#9fcde8 35%,#2b9bc9 55%,#1a86b8 80%,#e8e8e6 100%)}
.hero-copy{left:110px;top:155px;font-family:"Ubuntu",sans-serif}
.hero-copy .small{font-size:22px;color:var(--blue)}
.hero-copy h1{font-size:30px;font-weight:500;color:var(--blue);display:flex;align-items:center;gap:10px;white-space:nowrap;border-bottom:1px solid rgba(255,255,255,.7);padding-bottom:4px;width:280px}
.hero-copy p{color:#fff;font-size:13px;line-height:20px;margin-top:6px}

/* search panel */
.finder{left:647px;top:103px;width:252px;height:409px;background:var(--panel);border-top:3px solid var(--green);padding:10px 11px;color:#fff;font-family:"Ubuntu",sans-serif}
.finder h2{font-weight:400;font-size:21px;letter-spacing:.3px}
.finder .lead{font-size:13px;line-height:20px;margin:2px 0 10px}
.field{background:#fff;color:#555;font-size:10.5px;height:25px;line-height:25px;padding-left:11px;margin-bottom:10px;position:relative}
.field::after{content:"";position:absolute;right:0;top:0;border-top:12px solid #5ab0e0;border-left:12px solid transparent}
.field.wide{width:233px}
.pair{display:flex;gap:10px}
.pair .field{width:103px}
.checks{font-size:9.5px;line-height:14.5px;margin-top:-2px}
.checks div{display:flex;align-items:center;gap:8px}
.checks i{width:10px;height:10px;background:#fff;display:inline-block;position:relative}
.checks i.on::after{content:"";position:absolute;left:3px;top:1px;width:3px;height:6px;border:solid var(--blue-dark);border-width:0 1.5px 1.5px 0;transform:rotate(45deg)}
.cta{display:block;margin:14px auto 0;width:136px;height:31px;line-height:31px;text-align:center;background:var(--green);font-weight:500;font-size:13px;border-radius:2px}

/* service tabs */
.tabs{left:100px;top:364px;width:175px}
.tab{height:36px;background:var(--tab);border-bottom:1px solid #cfcfcf;display:flex;align-items:center;gap:14px;padding-left:14px;font-family:"Ubuntu",sans-serif;font-size:13px;color:#444}
.tab.active{background:var(--green);color:#fff}
.tab svg{width:24px;height:18px}
.service{left:275px;top:364px;width:372px;height:148px;background:#efefef;padding:10px 11px}
.service h3{font-family:"Ubuntu",sans-serif;font-weight:400;font-size:16px;color:var(--blue)}
.service p{font-size:10px;line-height:18.3px;margin-top:4px;color:#999}
.service a{font-size:11px;color:var(--blue-dark);text-decoration:underline}

/* welcome */
.section-title{font-family:"Ubuntu",sans-serif;font-weight:500;font-size:19px;color:var(--blue);border-left:3px solid var(--blue);padding-left:11px;line-height:25px}
.welcome{left:100px;top:532px;width:540px}
.welcome .body{padding-left:13px;font-size:10.5px;line-height:19.2px;font-weight:300;color:#777}
.welcome .body p{margin-top:6px}
.testimonials{left:656px;top:532px;width:240px}
.quote{display:flex;gap:9px;margin-left:14px;margin-top:10px}
.avatar{width:38px;height:38px;flex:none;background:#d6d6d6;border:1px solid #ccc}
.quote b{font-weight:400;color:var(--green);font-size:10.5px}
.quote p{font-size:9.5px;line-height:16.6px;color:#aaa;margin-top:4px}

/* trips */
.trips{left:0;top:749px;width:998px;height:237px;background:var(--band)}
.trips-head{top:768px;left:0;width:998px;display:flex;justify-content:center;align-items:center;font-family:"Ubuntu",sans-serif;font-size:12.5px;color:var(--blue-dark);gap:22px}
.trips-line{top:776px;height:1px;background:#d8d8d8}
.trip{top:799px;width:183px}
.trip .photo{height:117px;background:#fff;padding:5px;box-shadow:0 0 0 1px #e2e2e2}
.trip .photo div{height:100%}
.trip h4{font-family:"Ubuntu",sans-serif;font-weight:400;font-size:13.5px;color:#444;margin:6px 0 0 5px}
.trip p{font-size:9.5px;line-height:12px;color:#999;margin-left:4px}

/* footer */
.footer{left:0;top:986px;width:998px;height:172px;background:var(--footer)}
.fcol{top:1004px;font-family:"Ubuntu",sans-serif;color:#d0d0d0}
.fcol h5{font-weight:400;font-size:13.5px;color:#fff;margin-bottom:11px}
.fcol li{list-style:none;font-size:10.5px;line-height:19.2px}
.vline{top:1036px;width:1px;height:108px;background:var(--footer-line)}
.bottom{left:0;top:1158px;width:998px;height:42px;background:var(--footer);border-top:1px solid var(--footer-line);font-family:"Ubuntu",sans-serif;font-size:10.5px;color:#e0e0e0;display:flex;justify-content:space-between;align-items:center;padding:0 104px 0 105px}
</style>
</head>
<body>

<header>
  <div class="abs brand"><span class="brand-dot"></span>belvascotravel.com</div>
  <div class="abs social">
    <span aria-label="Social profile"></span>
    <span aria-label="Social profile"></span>
    <span aria-label="Search"><svg width="11" height="11" viewBox="0 0 11 11"><circle cx="4.5" cy="4.5" r="3.2" fill="none" stroke="#fff" stroke-width="1.5"/><line x1="7" y1="7" x2="10" y2="10" stroke="#fff" stroke-width="1.6"/></svg></span>
  </div>
  <div class="abs callout">YOU CALL, WE'RE THERE<br>(866-BVTRAVL)</div>
  <nav class="abs nav">
    <a class="active" href="#">Home</a><a href="#">Products</a><a href="#">Blog</a><a href="#">Freebies</a><a href="#">Member Login</a>
  </nav>
</header>

<section>
  <div class="abs hero" role="img" aria-label="Couple sitting on a white balustrade overlooking a turquoise sea"></div>
  <div class="abs hero-copy">
    <div class="small">You Are</div>
    <h1>Belvasco Travel
      <svg width="26" height="26" viewBox="0 0 26 26"><circle cx="13" cy="13" r="11.5" fill="none" stroke="#2f5fb3" stroke-width="2"/><path d="M11 8l5 5-5 5" fill="none" stroke="#2f5fb3" stroke-width="2"/></svg>
    </h1>
    <p>Lorem Ipsum est simplement du faux<br>text Lorem Ipsum est</p>
  </div>

  <form class="abs finder">
    <h2>FIND A PLACE TO STAY</h2>
    <p class="lead">Lorem Ipsum est simplement du faux text Lorem Ipsum est</p>
    <div class="field wide">Where do you want to go?</div>
    <div class="field wide">Persons</div>
    <div class="field wide">Range</div>
    <div class="field wide">Range</div>
    <div class="pair"><div class="field">Lorem Ipsum</div><div class="field">Lorem Ipsum</div></div>
    <div class="pair"><div class="field">Lorem Ipsum</div><div class="field">Lorem Ipsum</div></div>
    <div class="checks">
      <div><i></i>Обратно</div>
      <div><i class="on"></i>В одну сторону</div>
      <div><i></i>Обратно</div>
      <div><i class="on"></i>В одну сторону</div>
    </div>
    <span class="cta">GET YOURS NOW</span>
  </form>

  <div class="abs tabs">
    <div class="tab active"><svg viewBox="0 0 24 18"><circle cx="15" cy="3" r="2" fill="#fff"/><path d="M14 6l-4 5-4 1M14 6l1 5 4 4M12 11l-3 6M19 7l3 1" stroke="#fff" stroke-width="1.8" fill="none"/></svg>Visa Service</div>
    <div class="tab"><svg viewBox="0 0 24 18"><path d="M2 9h20M12 9l-5-6M12 9l-5 6M20 9l2-3" stroke="#444" stroke-width="2" fill="none"/></svg>Flights Service</div>
    <div class="tab"><svg viewBox="0 0 24 18"><rect x="2" y="9" width="20" height="4" fill="#444"/><rect x="2" y="4" width="2" height="11" fill="#444"/><rect x="20" y="9" width="2" height="6" fill="#444"/><rect x="6" y="6" width="5" height="3" fill="#444"/></svg>Hotel Service</div>
    <div class="tab"><svg viewBox="0 0 24 18"><path d="M5 15L17 3M5 3l12 12" stroke="#444" stroke-width="2.4"/></svg>Other Services</div>
  </div>
  <div class="abs service">
    <h3>Visa Services</h3>
    <p>Lorem Ipsum est simplement du fax text employé dans la sition page avant impression.Lorem Ipsum est le faux texte standard primerie depuis années 1500, quand un peintre anony me assembla ensemble des morceaux de texte pour quand un réaliser un livre spécimen de polices de texte.</p>
    <a href="#">View Detail</a>
  </div>
</section>

<section class="abs welcome">
  <h2 class="section-title">Welcome to Belvasco Travel</h2>
  <div class="body">
    <p style="margin-top:10px">Lorem Ipsum est simplement du faux texte employé dans la sition et la misen page avant impression. Le Lorem Ipsum est le faux texte standard de l'imprimerie depuis les années 1500, quand un peintre anonyme assembla ensemble des morceaux de texte pour réaliser un livre spécimen de polices de texte.</p>
    <p>Il n'a pas fait que survivre cinq siècles, mais s'est aussi adapté à la bureautique informatique, sans que son contenu n'en soit modifié. Il a été popularisé dans les années 1960.<br>&nbsp;grâce à la vente de feuilles Pressmark contenant des passages du Lorem Ipsum, et, plus récemment, par son inclusion dans des applications de mise en page de texte, comme Quillset Layout.</p>
  </div>
</section>

<section class="abs testimonials">
  <h2 class="section-title">Testimonials</h2>
  <div class="quote"><div class="avatar" role="img" aria-label="Client portrait"></div><div><b>Aldous Wenmark</b><p>"Lo1rem ipsum dolor sit nsectetuer adipiscing elit, sed diam nummy nibh euismod."</p></div></div>
  <div class="quote" style="margin-top:12px"><div class="avatar" role="img" aria-label="Client portrait"></div><div><b>Andrew Sallow</b><p>"Lo1rem ipsum dolor sit nsectetuer adipiscing elit, sed diam nummy nibh specimen de polices euismod."</p></div></div>
</section>

<section>
  <div class="abs trips"></div>
  <div class="abs trips-line" style="left:0;width:382px"></div>
  <div class="abs trips-line" style="left:632px;width:366px"></div>
  <div class="abs trips-head">
    <svg width="8" height="13" viewBox="0 0 8 13"><path d="M7 1L2 6.5 7 12" fill="none" stroke="#b5b5b5" stroke-width="2"/></svg>
    <span>Some Of Our Client Trip Photos</span>
    <svg width="8" height="13" viewBox="0 0 8 13"><path d="M1 1l5 5.5L1 12" fill="none" stroke="#b5b5b5" stroke-width="2"/></svg>
  </div>
  <div class="abs trip" style="left:117px"><div class="photo"><div role="img" aria-label="Beach umbrella and deck chairs on the sand" style="background:linear-gradient(180deg,#6fb4e8,#bfe0f4 60%,#eee6d6)"></div></div><h4>January Trip</h4><p>Lorem Ipsum est simplement du faux texte employé dans.</p></div>
  <div class="abs trip" style="left:311px"><div class="photo"><div role="img" aria-label="Swimmer holding a surfboard above the sea" style="background:linear-gradient(180deg,#c9ecf6,#49b7d8 55%,#1e9fc6)"></div></div><h4>March Trip</h4><p>Lorem Ipsum est simplement du faux texte employé dans.</p></div>
  <div class="abs trip" style="left:503px"><div class="photo"><div role="img" aria-label="Family cheering beside a yellow car" style="background:linear-gradient(90deg,#f0b43a,#e05a6a 40%,#d9403a 65%,#8fc6ea)"></div></div><h4>August Trip</h4><p>Lorem Ipsum est simplement du faux texte employé dans.</p></div>
  <div class="abs trip" style="left:699px"><div class="photo"><div role="img" aria-label="Children running along a sunny beach" style="background:linear-gradient(180deg,#8fc4ea,#cfe6f2 45%,#e9e1cf)"></div></div><h4>December Trip</h4><p>Lorem Ipsum est simplement du faux texte employé dans.</p></div>
</section>

<footer>
  <div class="abs footer"></div>
  <div class="abs fcol" style="left:106px"><h5>DESTINATIONS:</h5><ul><li>Europe</li><li>North America</li><li>South America</li><li>Africa</li><li>Asia</li><li>Australia</li></ul></div>
  <div class="abs vline" style="left:248px"></div>
  <div class="abs fcol" style="left:301px"><h5>SITE MAP</h5><ul><li>Home</li><li>Activites</li><li>Trip Styles</li><li>Responsible Travel</li></ul></div>
  <div class="abs vline" style="left:458px"></div>
  <div class="abs fcol" style="left:491px"><h5>OUR SERVICES</h5><ul><li>Lorem ipsum dolor</li><li>Sit amet consecteture</li><li>Adipiscing elit</li><li>Son inclusin dans des</li></ul></div>
  <div class="abs vline" style="left:695px"></div>
  <div class="abs fcol" style="left:731px"><h5>CONTACT INFORMATIONS:</h5><ul><li>E-mail: hello@belvascotravel.com</li><li>Phone: +47 55 10 24 68</li><li>Opening hours:</li><li>Mon - Fri: 09.00 - 21.00</li><li>Sat: 12.00 - 16.00</li><li>Sun: 12.00 - 14.00</li></ul></div>
  <div class="abs bottom"><span>Copyright 2013 Website Name. All Rights Reserved.</span><span>Privacy Policy | Terms &amp; Condition</span></div>
</footer>

</body>
</html>
```